Looking for someone to design a business card for my plumbing business Quandor Plumbing Solutions I want the background also to be black, must attract clients. If possible I want the front to be the logo and the back to show maybe the details.

Target Market(s)

Clients

Industry/Entity Type

Plumbing maintenance

Contact Information for Business Card

Name: Felix, Contact: 0461 539 207, Email: quandorplumbingsolutions@mailbrook.example, Licence number 728093K

Font styles to use
Other font styles liked:
• as per logo maybe?

Colors

Designer to choose colors to be used in the design.

Requirements
Nice to have
• stating the service I provide, emergency plumbing, plumbing maintenance, drainage maintenance, block sewer and stormwater, camera and locating.

```html
<!DOCTYPE html>
<html lang="en">
<head>
<meta charset="utf-8">
<title>Quandor Plumbing Solutions – Business Card</title>
<link rel="stylesheet" href="https://fonts.googleapis.com/css2?family=Montserrat:wght@400;500;700;800&display=swap">
<style>
  :root {
    --backdrop: #161616;
    --card: #232323;
    --blue: #4a90d2;
    --white: #f2f2f2;
    --text: #e6e6e6;
  }
  * { margin: 0; padding: 0; box-sizing: border-box; }
  html, body { width: 1200px; height: 1059px; overflow: hidden; background: var(--backdrop); }
  body { position: relative; font-family: "Montserrat", sans-serif; color: var(--text); }

  .card {
    position: absolute;
    left: 255px;
    width: 690px;
    height: 392px;
    background: var(--card);
    border-radius: 18px;
    box-shadow: 0 10px 24px rgba(0,0,0,.55);
  }
  .card--details { top: 89px; }
  .card--front { top: 547px; }

  /* brand name */
  .brand { color: var(--white); font-weight: 800; text-transform: uppercase; line-height: 1; }
  .brand__mark { display: inline-block; border-radius: 50%; background: var(--blue); }
  .card--details .brand-block {
    position: absolute; right: 38px; top: 60px;
    display: flex; align-items: center; gap: 14px;
  }
  .card--details .brand__mark { width: 44px; height: 44px; }
  .card--details .brand { font-size: 22px; text-align: right; letter-spacing: .5px; }
  .card--details .brand span { display: block; }
  .card--details .brand .brand__line-sub { font-size: 13px; margin-top: 6px; letter-spacing: .8px; }

  .card--front .brand-block {
    position: absolute; left: 0; right: 0; top: 0; bottom: 0;
    display: flex; align-items: center; justify-content: center; gap: 22px;
  }
  .card--front .brand__mark { width: 78px; height: 78px; }
  .card--front .brand { font-size: 54px; letter-spacing: 1px; }
  .card--front .brand span { display: block; }
  .card--front .brand .brand__line-sub { font-size: 22px; margin-top: 10px; letter-spacing: 1.2px; }

  /* person */
  .person { position: absolute; left: 35px; top: 162px; }
  .person__name { font-size: 28px; font-weight: 800; color: var(--blue); letter-spacing: .5px; line-height: 1; }
  .person__role { font-size: 15px; font-weight: 400; margin-top: 5px; }

  .divider { position: absolute; left: 35px; right: 38px; top: 228px; height: 1px; background: var(--blue); }

  /* contacts */
  .contacts { position: absolute; left: 35px; top: 249px; list-style: none; font-size: 14.5px; }
  .contacts li { display: flex; align-items: center; gap: 8px; height: 27px; }
  .contacts li.licence { height: 32px; align-items: flex-start; padding-top: 0; }
  .contacts .icon { width: 13px; height: 13px; flex: none; fill: var(--blue); }
  .contacts .social-dot { width: 13px; height: 13px; border-radius: 50%; background: var(--blue); flex: none; }

  /* services */
  .services { position: absolute; right: 38px; top: 249px; list-style: none; text-align: right; font-size: 14.5px; }
  .services li { height: 21.7px; display: flex; justify-content: flex-end; align-items: center; gap: 6px; }
  .services li::after { content: ""; width: 5px; height: 5px; border-radius: 50%; background: var(--blue); }
</style>
</head>
<body>

<section class="card card--details">
  <div class="brand-block">
    <p class="brand"><span>Quandor</span><span class="brand__line-sub">Plumbing Solutions</span></p>
    <i class="brand__mark"></i>
  </div>

  <div class="person">
    <p class="person__name">FELIX</p>
    <p class="person__role">Founder &amp; CEO</p>
  </div>

  <div class="divider"></div>

  <ul class="contacts">
    <li class="licence">Licence number 728093K</li>
    <li>
      <svg class="icon" viewBox="0 0 24 24" aria-hidden="true"><path d="M6.6 10.8a15.1 15.1 0 0 0 6.6 6.6l2.2-2.2a1 1 0 0 1 1-.25 11.4 11.4 0 0 0 3.6.6 1 1 0 0 1 1 1V20a1 1 0 0 1-1 1A17 17 0 0 1 3 4a1 1 0 0 1 1-1h3.5a1 1 0 0 1 1 1c0 1.25.2 2.45.6 3.6a1 1 0 0 1-.25 1z"/></svg>
      0461 539 207
    </li>
    <li>
      <svg class="icon" viewBox="0 0 24 24" aria-hidden="true"><path d="M2 5h20v14H2z M3.5 6.5 12 13l8.5-6.5" fill="var(--blue)" stroke="var(--card)" stroke-width="1.5"/></svg>
      quandorplumbingsolutions@mailbrook.example
    </li>
    <li>
      <i class="social-dot"></i>
      @QuandorPlumbingSolutions
    </li>
  </ul>

  <ul class="services">
    <li>Emergency plumbing</li>
    <li>Plumbing maintenance</li>
    <li>Drainage maintenance</li>
    <li>Block sewer and stormwater</li>
    <li>Camera and locating</li>
  </ul>
</section>

<section class="card card--front">
  <div class="brand-block">
    <i class="brand__mark"></i>
    <p class="brand"><span>Quandor</span><span class="brand__line-sub">Plumbing Solutions</span></p>
  </div>
</section>

</body>
</html>
```